Preferred pricing vendor

We are a plumbing company that has many services
-Boilers & Controls
-Plumbing & Heating
-HVAC & Refrigeration
-Preventative Maintenacne
-Gas fitting & Drain Cleaning

We primarily look after condo buildings, and our preferred service rates ($98, $93, or $88 depending on the contract) extend to all of our clients. So in essence, we look after the mechanical room and common equipment but our clients can call us in for drain cleaning or replacing a fixture in their suite. The discounted rates apply to the personal residence. We want a flyer to let them know they get a discount on our services. A one-pager we can send out to all of our contract clients.

Included source files for our letterhead and logo just so you can see the colours we go with.

Target Market(s)

Residential repairs, individual people, replacement of fixtures in-suite specific repairs

Requirements
Must have
• be colourful and attractive

```html
<!DOCTYPE html>
<html lang="en">
<head>
<meta charset="utf-8">
<title>Keystone Mechanical Inc – Service Flyer</title>
<link href="https://fonts.googleapis.com/css2?family=Anton&family=Barlow+Condensed:ital,wght@0,700;1,700;1,800&family=Comfortaa:wght@700&display=swap" rel="stylesheet">
<style>
  :root {
    --blue: #1f73c4;
    --blue-deep: #0a6ac9;
    --orange: #f15a29;
    --mauve: #86606e;
    --ink: #1b1b1b;
    --white: #ffffff;
    --tick: #4cc21c;
    --badge-shadow: #8a2a12;
    --paper-shadow: rgba(0,0,0,0.28);
  }
  * { margin: 0; padding: 0; box-sizing: border-box; }
  html, body { width: 848px; height: 1200px; overflow: hidden; background: var(--white); }
  .canvas { position: relative; width: 848px; height: 1200px; background: var(--white); }
  .flyer {
    position: absolute; left: 90px; top: 128px; width: 679px; height: 959px;
    background: var(--white); box-shadow: 5px 5px 6px var(--paper-shadow); overflow: hidden;
  }
  .bar { position: absolute; height: 24px; z-index: 5; }
  .bar--blue { left: 0; width: 449px; background: var(--blue); }
  .bar--orange { left: 455px; width: 224px; background: var(--orange); }
  .bar--top { top: 0; }
  .bar--bottom { bottom: 0; }

  .photo {
    position: absolute; left: 440px; top: 13px; width: 239px; height: 781px;
    background: linear-gradient(180deg, #f4b63a 0%, #f0d2c0 14%, #4f6c7a 32%, #46606c 52%, #2f3c5a 72%, #7c91a8 100%);
  }

  .brand {
    position: absolute; left: 40px; top: 0; width: 370px; text-align: center;
    font-family: "Barlow Condensed", sans-serif; font-weight: 700; color: var(--blue-deep);
  }
  .brand__dot { width: 68px; height: 68px; border-radius: 50%; background: var(--orange); margin: 79px auto 42px; }
  .brand__name { font-size: 56px; line-height: 1; letter-spacing: 3px; }
  .brand__sub { font-size: 20px; line-height: 1; letter-spacing: 5px; margin-top: 6px; }

  .headline-panel {
    position: absolute; left: 0; top: 284px; width: 440px; height: 291px;
    background: linear-gradient(90deg, var(--blue-deep) 0%, #3a6aa8 55%, var(--mauve) 100%);
  }
  .headline {
    position: absolute; left: 22px; top: 16px; width: 460px;
    font-family: "Barlow Condensed", sans-serif; font-style: italic; font-weight: 800;
    font-size: 60px; line-height: 64px; color: var(--white); text-transform: uppercase;
    text-shadow: 3px 3px 5px rgba(0,0,0,0.45);
  }
  .services-panel {
    position: absolute; left: 0; top: 575px; width: 376px; height: 177px;
    background: linear-gradient(90deg, var(--orange) 0%, #c8613f 45%, var(--mauve) 100%);
  }
  .services { list-style: none; position: absolute; left: 24px; top: 14px; }
  .services li {
    display: flex; align-items: center; height: 28.6px; white-space: nowrap;
    font-family: "Comfortaa", sans-serif; font-weight: 700; font-size: 19.5px; color: var(--white);
    text-shadow: 1px 1px 2px rgba(0,0,0,0.3);
  }
  .services svg { width: 28px; height: 22px; margin-right: 10px; flex: none; }

  .badge { position: absolute; left: 369px; top: 535px; width: 310px; height: 310px; z-index: 2; }
  .badge__text { font-family: "Anton", sans-serif; font-size: 54px; text-anchor: middle; fill: var(--white); }
  .badge__text--shadow { fill: var(--badge-shadow); }

  .rates-label {
    position: absolute; left: 75px; top: 812px; z-index: 4;
    font-family: "Barlow Condensed", sans-serif; font-style: italic; font-weight: 800;
    font-size: 34px; line-height: 34px; color: var(--ink); text-transform: uppercase; letter-spacing: 0.5px;
  }
  .rates-band { position: absolute; left: 24px; top: 852px; width: 655px; height: 68px; z-index: 4; }
  .rates-band svg { position: absolute; left: 0; top: 0; }
  .rates-band__text {
    position: absolute; left: 48px; right: 8px; top: 0; height: 68px; line-height: 68px; text-align: center;
    font-family: "Barlow Condensed", sans-serif; font-weight: 700; font-size: 32px; color: var(--white);
    text-transform: uppercase; letter-spacing: 0.5px; white-space: nowrap;
  }
</style>
</head>
<body>
<div class="canvas">
  <div class="flyer">
    <div class="bar bar--blue bar--top"></div>
    <div class="bar bar--orange bar--top"></div>

    <div class="photo" role="img" aria-label="Photo of a smiling plumber in a yellow hard hat and work shirt, carrying a toolbox and wearing a tool belt"></div>

    <div class="brand">
      <div class="brand__dot"></div>
      <div class="brand__name">KEYSTONE</div>
      <div class="brand__sub">MECHANICAL INC</div>
    </div>

    <div class="headline-panel">
      <h1 class="headline">We are a<br>plumbing company<br>that has many<br>services</h1>
    </div>

    <div class="services-panel">
      <ul class="services">
        <li><svg viewBox="0 0 30 24"><path d="M2 12 L11 21 L28 2" fill="none" stroke="var(--tick)" stroke-width="4" stroke-linecap="round" stroke-linejoin="round"/></svg>Boilers &amp; Controls</li>
        <li><svg viewBox="0 0 30 24"><path d="M2 12 L11 21 L28 2" fill="none" stroke="var(--tick)" stroke-width="4" stroke-linecap="round" stroke-linejoin="round"/></svg>Plumbing &amp; Heating</li>
        <li><svg viewBox="0 0 30 24"><path d="M2 12 L11 21 L28 2" fill="none" stroke="var(--tick)" stroke-width="4" stroke-linecap="round" stroke-linejoin="round"/></svg>HVAC &amp; Refrigeration</li>
        <li><svg viewBox="0 0 30 24"><path d="M2 12 L11 21 L28 2" fill="none" stroke="var(--tick)" stroke-width="4" stroke-linecap="round" stroke-linejoin="round"/></svg>Preventative Maintenacne</li>
        <li><svg viewBox="0 0 30 24"><path d="M2 12 L11 21 L28 2" fill="none" stroke="var(--tick)" stroke-width="4" stroke-linecap="round" stroke-linejoin="round"/></svg>Gas fitting &amp; Drain Cleaning</li>
      </ul>
    </div>

    <svg class="badge" viewBox="-160 -160 320 320">
      <polygon transform="rotate(8)" fill="var(--orange)" points="160,0 127.5,34.2 138.6,80 93.3,93.3 80,138.6 34.2,127.5 0,160 -34.2,127.5 -80,138.6 -93.3,93.3 -138.6,80 -127.5,34.2 -160,0 -127.5,-34.2 -138.6,-80 -93.3,-93.3 -80,-138.6 -34.2,-127.5 0,-160 34.2,-127.5 80,-138.6 93.3,-93.3 138.6,-80 127.5,-34.2"/>
      <g transform="rotate(-14)">
        <g transform="translate(3,3)">
          <text class="badge__text badge__text--shadow" x="6" y="-34">SPECIAL</text>
          <text class="badge__text badge__text--shadow" x="0" y="20">DISCOUNT</text>
          <text class="badge__text badge__text--shadow" x="-6" y="74">AVAILABLE</text>
        </g>
        <text class="badge__text" x="6" y="-34">SPECIAL</text>
        <text class="badge__text" x="0" y="20">DISCOUNT</text>
        <text class="badge__text" x="-6" y="74">AVAILABLE</text>
      </g>
    </svg>

    <div class="rates-label">Service rates:</div>
    <div class="rates-band">
      <svg width="655" height="68" viewBox="0 0 655 68"><polygon points="48,0 655,0 655,68 0,68" fill="var(--blue-deep)"/></svg>
      <div class="rates-band__text">($98, $93, or $88 depending on the contract)</div>
    </div>

    <div class="bar bar--blue bar--bottom"></div>
    <div class="bar bar--orange bar--bottom"></div>
  </div>
</div>
</body>
</html>
```